The Brightwater Hour (By Line: Making an Impact through Effective Leadership)

I am seeking the design and creation of a”banner ad image” for my radio program entitled “The Brightwater Hour.” The banner created should capture the look and feel of an image that reflects the vision statement below and that fosters the intent reflected by the principal goals listed below:

Vision statement

The Brightwater Hour is a powerfully engaging platform for great conversations about leadership and leadership learning.

Goals

1. Build a community of listeners who will be made to feel invited and excited about being connected to the show, it host and its broader community of listeners.

2. Provide interesting, intelligent and meaningful conversations about leadership and learning by the host, invited guests, both in studio and online.
The banner should be one that speaks to/invites listeners to become members of a community of listeners seeking to listen to and learn about the subject of leadership and leadership improvement.

The acceptable (final) banner should be professional in image, style and substance. The Photo shop layered file is required so that the banner image can be altered and adapted for use in PDF or text documents.

Finally, it is a banner that I intend to repopulate across several medium’s, such as pelzor, grip tally, etc. as a part of the process of establishing an image – brand – for the radio show as reflected the vision statement and goals.

While the target audience described is broad, it is anticipated that the primary listeners will be those who are leaders and serving in such roles as CEO’s, Vice Presidents, and other leaders in business, government and other local organizational capacities including students interested in learning about and discussing the subject of leadership.

Target Market(s)

Those who are interested in the topic of leadership and are actively engaged in leading as supervisors, managers and executives. These would be CEO, VP, and other C-level leaders in business, private and public sector organizations. It is also anticipated that those who are students of leadership learning will find my program a great resource.

Industry/Entity Type

Radio

Colors
3176b5
b768aa
d3a5cc

Requirements
Must have
• Be unique, attractive and capture the look and feel as noted in the description of the project.
Nice to have
• Note: I will have a head shot photo included in the banner so a place holder needs to be included for that

```html
<!DOCTYPE html>
<html lang="en">
<head>
<meta charset="UTF-8">
<title>The Brightwater Hour – Banner</title>
<link href="https://fonts.googleapis.com/css2?family=Open+Sans:wght@600&family=Source+Sans+3:wght@300;400&display=swap" rel="stylesheet">
<style>
  :root {
    --page-bg: #e5e5e5;
    --card-bg: #ffffff;
    --brand-purple: #b768aa;
    --brand-purple-dark: #9a5690;
    --brand-purple-light: #d3a5cc;
    --brand-blue: #3176b5;
    --brand-blue-light: #4a88c0;
    --body-text: #7a7a7a;
    --white: #ffffff;
  }
  html, body {
    margin: 0;
    padding: 0;
    width: 1200px;
    height: 1200px;
    overflow: hidden;
    background: var(--page-bg);
  }
  .banner {
    position: absolute;
    left: 249px;
    top: 50px;
    width: 702px;
    height: 1100px;
    background: var(--card-bg);
    overflow: hidden;
  }
  .banner__photo {
    position: absolute;
    left: 0;
    top: 0;
    width: 702px;
    height: 450px;
    background: linear-gradient(180deg, #c9ccd2 0%, #aab2bf 45%, #3a4a66 100%);
  }
  .banner__shapes {
    position: absolute;
    left: 0;
    top: 0;
    width: 702px;
    height: 1100px;
  }
  .banner__title {
    position: absolute;
    left: 0;
    top: 472px;
    width: 702px;
    margin: 0;
    text-align: center;
    font-family: "Open Sans", sans-serif;
    font-weight: 600;
    font-size: 74px;
    line-height: 96px;
    color: var(--white);
    letter-spacing: 0.5px;
  }
  .banner__vision {
    position: absolute;
    left: 78px;
    top: 739px;
    width: 546px;
    margin: 0;
    text-align: center;
    font-family: "Source Sans 3", sans-serif;
    font-weight: 400;
    font-size: 31px;
    line-height: 40px;
    color: var(--body-text);
  }
  .banner__cta {
    position: absolute;
    left: 112px;
    top: 960px;
    width: 481px;
    height: 111px;
    border-radius: 7px;
    background: linear-gradient(180deg, var(--brand-blue-light) 0%, var(--brand-blue-light) 50%, var(--brand-blue) 50%, var(--brand-blue) 100%);
    display: flex;
    align-items: center;
    justify-content: center;
    font-family: "Source Sans 3", sans-serif;
    font-weight: 300;
    font-size: 49px;
    color: var(--white);
    text-decoration: none;
    letter-spacing: 0.5px;
  }
</style>
</head>
<body>
  <main class="banner">
    <div class="banner__photo" role="img" aria-label="Photo of a group of smiling business professionals in suits, with the host headshot in front"></div>

    <svg class="banner__shapes" viewBox="0 0 476 746" preserveAspectRatio="none" aria-hidden="true">
      <polygon points="0,263 36,300 0,300" fill="var(--brand-purple-light)"/>
      <polygon points="0,300 476,283 476,445 438,441 0,400" fill="var(--brand-purple)"/>
      <polygon points="438,441 476,445 476,480" fill="var(--brand-purple-dark)"/>
    </svg>

    <h1 class="banner__title">Brightwater Hour</h1>

    <p class="banner__vision">The Brightwater Hour is a powerfully engaging platform for great conversations about leadership and leadership learning.</p>

    <a class="banner__cta" href="#">LEARN MORE</a>
  </main>
</body>
</html>
```